Determining number of boxes of planks of flooring for a room

Need a creative design of an infographic of a room with instructions on how to measure the room and use this measurement to determine how much flooring to order.
The floor planks come in boxes and each box has 36 planks. Each box covers 5 metre squared in total.
The intent of the infographic is to help inform the customer how many boxes they need to order for their room.
The infographic should match the style of flooring being sold (image provided) and the logo for the company (image provided).
A crude sketch of instructions to measure a room and determine the number of boxes is provided in a document attached with this brief. Need improvement to the steps mentioned in this document on the infographic created.

```html
<!DOCTYPE html>
<html lang="en">
<head>
<meta charset="utf-8">
<title>How to Work Out Room Size and Floor Packs</title>
<link rel="stylesheet" href="https://fonts.googleapis.com/css2?family=Montserrat:wght@600;700;800&display=swap">
<style>
  :root {
    --page: #ffffff;
    --frame: #c3c9a0;
    --wall: #e6f1c6;
    --floor: #ebe7b0;
    --measure-red: #e8141b;
    --pack-blue: #2a7ae2;
    --ink: #111111;
    --wall-ink: #4a4c37;
    --note-ink: #3a3a3a;
    --bubble: rgba(255, 255, 255, 0.86);
  }
  html, body {
    margin: 0;
    padding: 0;
    width: 1200px;
    height: 1144px;
    overflow: hidden;
    background: var(--page);
  }
  .infographic {
    display: block;
    width: 1200px;
    height: 1144px;
    font-family: "Montserrat", Arial, sans-serif;
  }
  .wall-title {
    font-weight: 700;
    font-size: 44px;
    fill: var(--wall-ink);
  }
  .measure-line { stroke: var(--measure-red); stroke-width: 4; fill: none; }
  .measure-tick { stroke: var(--measure-red); stroke-width: 5; }
  .measure-label { fill: var(--measure-red); font-weight: 700; font-size: 27px; }
  .step-bubble { fill: var(--bubble); }
  .step-number { font-weight: 800; font-size: 34px; fill: var(--ink); }
  .step-heading { font-weight: 700; font-size: 26px; fill: var(--ink); }
  .accent-red { fill: var(--measure-red); }
  .accent-blue { fill: var(--pack-blue); }
  .step-formula { font-weight: 700; font-size: 26px; }
  .step-note { font-weight: 600; font-size: 13.5px; fill: var(--note-ink); }
  .brand-name { font-weight: 700; font-size: 40px; fill: var(--wall-ink); letter-spacing: 1px; }
  .brand-mark { fill: var(--wall-ink); }
</style>
</head>
<body>
<svg class="infographic" viewBox="0 0 1200 1144" xmlns="http://www.w3.org/2000/svg">
  <defs>
    <linearGradient id="roomTones" x1="0" y1="0" x2="0" y2="1">
      <stop offset="0" stop-color="#e6f1c6"/>
      <stop offset="0.6" stop-color="#eef5cc"/>
      <stop offset="1" stop-color="#ebe7b0"/>
    </linearGradient>
  </defs>

  <g class="room-illustration">
    <polygon points="538,0 1200,280 1200,881 665,1144 0,834 0,254" fill="var(--frame)"/>
    <polygon role="img" aria-label="Isometric illustration of an empty room with a doorway, two windows and a plank floor"
             points="546,22 1170,300 1170,866 665,1110 30,818 30,270" fill="url(#roomTones)"/>
  </g>

  <text class="wall-title" transform="translate(96,303) rotate(-27.5)" textLength="478" lengthAdjust="spacingAndGlyphs">HOW TO WORK OUT</text>
  <text class="wall-title" transform="translate(561,108) rotate(26.6)" textLength="648" lengthAdjust="spacingAndGlyphs">ROOM SIZE AND FLOOR PACKS</text>

  <g class="room-measurements">
    <line class="measure-line" x1="73" y1="370" x2="546" y2="127"/>
    <line class="measure-line" x1="546" y1="127" x2="1135" y2="415"/>
    <line class="measure-tick" x1="50" y1="359" x2="101" y2="384"/>
    <line class="measure-tick" x1="505" y1="140" x2="556" y2="118"/>
    <line class="measure-tick" x1="536" y1="118" x2="596" y2="147"/>
    <line class="measure-tick" x1="1116" y1="432" x2="1159" y2="412"/>
    <text class="measure-label" x="322" y="284">a</text>
    <text class="measure-label" x="825" y="310">b</text>
  </g>

  <g class="step step-measure" text-anchor="middle">
    <circle class="step-bubble" cx="542" cy="400" r="199"/>
    <text class="step-number" x="542" y="289">1</text>
    <text class="step-heading" x="542" y="321">Measure</text>
    <text class="step-heading" x="542" y="353">Room Dimensions <tspan class="accent-red">[c]</tspan></text>
    <text class="step-formula accent-red" x="542" y="385">c = a x b</text>
    <text class="step-note" x="542" y="446">a » room length</text>
    <text class="step-note" x="542" y="463">b » room width</text>
    <text class="step-note" x="542" y="497">(If your room is not a square shape,</text>
    <text class="step-note" x="542" y="514">please do a simple drawing and</text>
    <text class="step-note" x="542" y="531">send it to us. We will be able to</text>
    <text class="step-note" x="542" y="548">work it out for you).</text>
  </g>

  <g class="step step-packs" text-anchor="middle">
    <circle class="step-bubble" cx="665" cy="864" r="199"/>
    <text class="step-number" x="665" y="746">2</text>
    <text class="step-heading" x="665" y="778">Work Out</text>
    <text class="step-heading" x="665" y="810">Pack Number <tspan class="accent-blue">[d]</tspan></text>
    <text class="step-formula accent-blue" x="665" y="842">d = c / 5</text>
    <text class="step-note" x="665" y="897">c » room dimention</text>
    <text class="step-note" x="665" y="914">5 » 5 m² coverage of 1 pack (36 planks)</text>
    <text class="step-note" x="665" y="948">If d has decimal points, please always</text>
    <text class="step-note" x="665" y="965">round up to the next integer.</text>
    <text class="step-note" x="665" y="982">[e.g. if d = 3.1, then d needs to be 4.</text>
    <text class="step-note" x="665" y="999">Or if d = 3.8, d still needs to be 4].</text>
  </g>

  <g class="brand">
    <rect class="brand-mark" x="90" y="1036" width="34" height="34"/>
    <text class="brand-name" x="138" y="1068">TERRAVALE</text>
  </g>
</svg>
</body>
</html>
```